Business Card Design (NEW FILES)

ATTENTION: New vector files are available. Please update your design to reflect/use the new (better resolution) logo images.

Seeking a unique and professional business card design for a commercial drone photography/videography business. The layout should feature
the logo (attached) and include the following information:
Owen Tarrick
614-502-7738
www.skylarkreelworks.example
NRD Certified Remote Pilot

Owen Tarrick

```html
<!DOCTYPE html>
<html lang="en">
<head>
<meta charset="utf-8">
<title>Skylark Reelworks – Business Card</title>
<link rel="stylesheet" href="https://fonts.googleapis.com/css2?family=Montserrat:wght@500;700&family=Open+Sans:wght@400;600&display=swap">
<style>
  :root {
    --bg: #222222;
    --card: #ffffff;
    --navy: #1b1f4b;
    --orange: #ef8a47;
    --swoosh-dark: #d9dadd;
    --swoosh-light: #f4f4f5;
  }
  * { margin: 0; padding: 0; box-sizing: border-box; }
  html, body { width: 1200px; height: 780px; overflow: hidden; background: var(--bg); }
  .stage { position: relative; width: 1200px; height: 780px; }
  .card {
    position: absolute; top: 92px; width: 340px; height: 595px;
    background: var(--card); border-radius: 24px; overflow: hidden;
    box-shadow: 0 10px 30px rgba(0,0,0,.45);
  }
  .card--front { left: 230px; }
  .card--back { left: 630px; }

  /* Front */
  .front-mark {
    position: absolute; left: 50%; top: 50%;
    transform: translate(-50%, -50%) rotate(-90deg);
    display: flex; align-items: center; gap: 14px; white-space: nowrap;
  }
  .brand-name {
    font-family: "Montserrat", sans-serif; font-weight: 500;
    color: var(--navy); letter-spacing: .04em; text-transform: uppercase;
  }
  .front-mark .brand-name { font-size: 40px; }
  .brand-dot { border-radius: 50%; background: var(--orange); flex: none; }
  .front-mark .brand-dot { width: 34px; height: 34px; }

  /* Back */
  .back-mark {
    position: absolute; top: 62px; left: 0; right: 0;
    display: flex; justify-content: center; align-items: center; gap: 9px;
  }
  .back-mark .brand-name { font-size: 22px; }
  .back-mark .brand-dot { width: 18px; height: 18px; }

  .swoosh { position: absolute; inset: 0; width: 100%; height: 100%; }

  .person {
    position: absolute; top: 188px; left: 0; right: 0; text-align: center;
    font-family: "Montserrat", sans-serif;
  }
  .person__name { font-size: 27px; font-weight: 700; }
  .person__first { color: var(--orange); }
  .person__last { color: var(--navy); }
  .person__role { font-size: 13px; font-weight: 700; color: var(--navy); margin-top: 2px; }

  .contact-icons { display: flex; justify-content: center; gap: 8px; margin-top: 16px; }
  .contact-icon {
    width: 24px; height: 24px; border-radius: 50%; background: var(--orange);
    display: flex; align-items: center; justify-content: center;
  }
  .contact-icon svg { width: 13px; height: 13px; }
  .contact-list {
    list-style: none; margin-top: 10px;
    font-family: "Open Sans", sans-serif; font-weight: 600; font-size: 13px;
    color: var(--navy); line-height: 1.45;
  }

  .credentials {
    position: absolute; bottom: 58px; left: 0; right: 0; text-align: center;
    font-family: "Open Sans", sans-serif; font-weight: 600; font-size: 13.5px;
    color: var(--navy); line-height: 1.5;
  }
</style>
</head>
<body>
<main class="stage">

  <section class="card card--front" aria-label="Card front">
    <div class="front-mark">
      <span class="brand-dot"></span>
      <span class="brand-name">Skylark Reelworks</span>
    </div>
  </section>

  <section class="card card--back" aria-label="Card back">
    <svg class="swoosh" viewBox="0 0 340 595" preserveAspectRatio="none" aria-hidden="true">
      <defs>
        <linearGradient id="swoosh-shade" x1="0" y1="0" x2="0" y2="1">
          <stop offset="0" stop-color="var(--swoosh-dark)"/>
          <stop offset="1" stop-color="var(--swoosh-light)"/>
        </linearGradient>
      </defs>
      <path d="M0 405 C110 420 250 380 340 300 L340 595 L0 595 Z" fill="url(#swoosh-shade)"/>
      <path d="M0 400 C120 412 260 360 340 250 L340 300 C250 380 110 420 0 405 Z" fill="#fff"/>
      <path d="M60 595 C140 520 220 450 340 400 L340 595 Z" fill="url(#swoosh-shade)"/>
      <path d="M40 595 C130 505 220 435 340 385 L340 400 C220 450 140 520 60 595 Z" fill="#fff"/>
    </svg>

    <div class="back-mark">
      <span class="brand-name">Skylark Reelworks</span>
      <span class="brand-dot"></span>
    </div>

    <div class="person">
      <p class="person__name"><span class="person__first">Owen</span> <span class="person__last">Tarrick</span></p>
      <p class="person__role">Owner</p>

      <div class="contact-icons">
        <span class="contact-icon" aria-label="Phone">
          <svg viewBox="0 0 24 24" fill="#fff"><path d="M6.6 10.8a15 15 0 0 0 6.6 6.6l2.2-2.2c.3-.3.7-.4 1-.2 1.1.4 2.3.6 3.6.6.6 0 1 .4 1 1V20c0 .6-.4 1-1 1A17 17 0 0 1 3 4c0-.6.4-1 1-1h3.5c.6 0 1 .4 1 1 0 1.3.2 2.5.6 3.6.1.3 0 .7-.2 1z"/></svg>
        </span>
        <span class="contact-icon" aria-label="Email">
          <svg viewBox="0 0 24 24" fill="none" stroke="#fff" stroke-width="2"><rect x="3" y="5" width="18" height="14" rx="2"/><path d="M3 7l9 6 9-6"/></svg>
        </span>
        <span class="contact-icon" aria-label="Website">
          <svg viewBox="0 0 24 24" fill="none" stroke="#fff" stroke-width="2"><circle cx="12" cy="12" r="9"/><path d="M3 12h18M12 3c3 3 3 15 0 18M12 3c-3 3-3 15 0 18"/></svg>
        </span>
      </div>

      <ul class="contact-list">
        <li>614-502-7738</li>
        <li>www.skylarkreelworks.example</li>
        <li>info@skylarkreelworks.example</li>
      </ul>
    </div>

    <p class="credentials">NRD Certified Remote Pilot<br>Fully Insured</p>
  </section>

</main>
</body>
</html>
```